brovlanepass.net

Develop a website for brolanepass.net will be a site to sell tickets for concerts, shows, shows, theaters and others. I need a web design easy view, very easy to use and accumulate events by date. The aim is to develop the site was connected to a complex system that is already developed. (Important this page to a robust system was connected via links the idea is to develop only the front view)
Updates

Reason: I need more designs yet we have not made the decision

Target Market(s)

millennials, adults, who want to enjoy concerts and shows

Industry/Entity Type

Event

Number of Pages Required

5+ page

Colors
1b1b1b
aaaaaa
ffffff

Requirements
Must have
• Easy Vista, accumulation of upcoming events, past events. The tabs should have are: 1 Start: In this part of upcoming events occur. You could put a banner on the top and down the events by date. 2. How to order: page with instructions on how to purchase tickets 3. About Us: The company history 4. Contact: Phones and template for contact by mail 5. Our policies: shopping 6. Notice Privacy: Privacy Notice Copoy 7. Centers Sale: physical places where they can purchase tickets Promoters 8. access: Link to a template
Nice to have
• as you can see p www.quimbarostage.net or farunda.net or farunda.org or gallowmerk.net (important this page to a robust system was connected via links the idea is to develop only the front view)
Should not have
• Many things Tangled

```html
<!DOCTYPE html>
<html lang="en">
<head>
<meta charset="utf-8">
<title>Brovlane Pass — Privacy</title>
<link href="https://fonts.googleapis.com/css2?family=Open+Sans:wght@400;600;700&family=Montserrat:wght@700&family=Roboto:wght@400&display=swap" rel="stylesheet">
<style>
  :root{
    --black:#000000;
    --nav-top:#2a2a2a;
    --nav-bottom:#141414;
    --ink:#1b1b1b;
    --grey:#aaaaaa;
    --white:#ffffff;
    --text:#d6cfd6;
    --red:#e0474a;
    --social:#2aa8e0;
    --content-a:#2a0a22;
    --content-b:#140510;
    --footer:#120c0e;
  }
  *{box-sizing:border-box;margin:0;padding:0}
  html,body{width:859px;height:1200px;overflow:hidden;background:var(--black)}
  body{position:relative;font-family:"Open Sans",sans-serif;color:var(--white)}

  .topbar{position:absolute;left:0;top:0;width:859px;height:80px;background:var(--black)}
  .phone{position:absolute;left:75px;top:24px;display:flex;align-items:center;gap:10px}
  .phone-icon{width:31px;height:31px;border:1.5px solid var(--white);border-radius:50%;display:flex;align-items:center;justify-content:center}
  .phone-number{font-family:"Roboto",sans-serif;font-size:16px;letter-spacing:.2px}
  .brand{position:absolute;left:376px;top:14px;width:107px;height:54px;background:var(--red);border-radius:4px;display:flex;align-items:center;justify-content:center}
  .brand span{font-weight:700;font-size:12px;color:var(--white);letter-spacing:.6px}
  .social{position:absolute;right:74px;top:30px;display:flex;gap:10px}
  .social i{display:block;width:17px;height:17px;border-radius:3px;background:var(--social)}
  .social i.alt{background:var(--red)}

  .mainnav{position:absolute;left:0;top:80px;width:859px;height:42px;background:linear-gradient(var(--nav-top),var(--nav-bottom))}
  .mainnav ul{list-style:none;position:absolute;left:70px;top:0;display:flex;height:42px}
  .mainnav li{position:relative;font-size:11.5px;line-height:42px;padding:0 17.5px;white-space:nowrap}
  .mainnav li.active{background:var(--black)}
  .mainnav li.active::before{content:"";position:absolute;left:0;right:0;top:0;height:2px;background:var(--red)}

  .hero{position:absolute;left:0;top:122px;width:859px;height:127px;background:linear-gradient(90deg,#120e14 0%,#2b2430 40%,#3a3848 65%,#1a1519 100%)}
  .hero h1{position:absolute;left:0;right:0;top:58px;text-align:center;font-family:"Montserrat",sans-serif;font-size:24px;letter-spacing:.5px}

  .content{position:absolute;left:0;top:249px;width:859px;height:743px;background:radial-gradient(ellipse at 60% 40%,var(--content-a),var(--content-b) 75%)}
  .notice{position:absolute;left:64px;top:26px;width:735px}
  .notice h2{font-weight:400;font-size:19px;line-height:26px;margin-bottom:7px}
  .notice h3{font-weight:400;font-size:15.5px;line-height:21px;margin:23px 0 5px 1px}
  .notice h3.tight{margin-top:17px}
  .notice p{font-size:10.3px;line-height:16.3px;color:var(--text);letter-spacing:-.1px;word-spacing:-.5px;hyphens:auto;-webkit-hyphens:auto}

  .footer{position:absolute;left:0;top:992px;width:859px;height:208px;background:linear-gradient(180deg,#1a1214,var(--footer))}
  .footer .brand{left:64px;top:62px}
  .col{position:absolute;top:42px}
  .col h4{font-weight:400;font-size:11.3px;margin-bottom:18px}
  .col p{font-size:8.6px;line-height:15.7px}
  .col-contact{left:245px}
  .col-mail{left:459px}
  .col-mail p{line-height:12px;width:150px;margin-top:-5px}
  .signup{display:flex;margin-top:6px}
  .signup span{width:105px;height:22px;background:var(--white);color:#8a8a8a;font-size:7.5px;line-height:22px;padding-left:6px}
  .signup b{width:40px;height:22px;background:#4a4a4a;font-weight:400;font-size:7.5px;line-height:22px;text-align:center}
  .col-follow{left:674px}
  .col-follow .social{position:static;gap:11px;margin-top:9px}
  .col-follow .social i{width:17px;height:17px;background:var(--white)}
  .rule{position:absolute;left:62px;top:160px;width:733px;height:1px;background:#3a3335}
  .copyright{position:absolute;left:0;right:0;top:178px;text-align:center;font-size:8.6px;padding-right:36px}
</style>
</head>
<body>
<header class="topbar">
  <div class="phone">
    <span class="phone-icon">
      <svg width="14" height="14" viewBox="0 0 24 24"><path fill="#fff" d="M6.6 10.8a15.1 15.1 0 0 0 6.6 6.6l2.2-2.2a1 1 0 0 1 1-.25 11.4 11.4 0 0 0 3.6.57 1 1 0 0 1 1 1V20a1 1 0 0 1-1 1A17 17 0 0 1 3 4a1 1 0 0 1 1-1h3.5a1 1 0 0 1 1 1c0 1.25.2 2.45.57 3.57a1 1 0 0 1-.25 1z"/></svg>
    </span>
    <span class="phone-number">+852 5550 1847</span>
  </div>
  <div class="brand"><span>BROVLANE PASS</span></div>
  <div class="social" aria-label="Social links"><i></i><i></i><i></i><i class="alt"></i></div>
</header>

<nav class="mainnav">
  <ul>
    <li>HOME</li><li>HOW TO ORDER</li><li>ABOUT US</li><li>CONTACT US</li><li>POLICIES</li><li class="active">PRIVACY</li><li>CENTER SALE</li><li>ACCESS</li>
  </ul>
</nav>

<section class="hero" role="img" aria-label="Darkened photo of a concert hall audience facing a lit stage">
  <h1>PRIVACY</h1>
</section>

<main class="content">
  <article class="notice">
    <h2>NOTICE OF PRIVACY</h2>
    <p>Lorem Ipsum is simply dummy text of the printing and typesetting industry. Lorem Ipsum has been the industry's standard dummy text ever since the 1500s, when an unknown printer took a galley of type and scrambled it to make a type specimen book. It has survived not only five centuries, but also the leap into electronic typesetting, remaining essentially unchanged. It was popularised in the 1960s with the release of Brindell sheets containing Lorem Ipsum passages, and more recently with desktop publishing software like Quillmark Layout including versions of Lorem Ipsum.</p>

    <h3>1. Neque porro quisquam est qui dolorem</h3>
    <p>It is a long established fact that a reader will be distracted by the readable content of a page when looking at its layout. The point of using Lorem Ipsum is that it has a more-or-less normal distribution of letters, as opposed to using 'Content here, content here', making it look like readable English. Many desktop publishing packages and web page editors now use Lorem Ipsum as their default model text, and a search for 'lorem ipsum' will uncover many web sites still in their infancy. Various versions have evolved over the years, sometimes by accident, sometimes on purpose.</p>

    <h3 class="tight">2. Dolorem ipsum quia dolor sit amet</h3>
    <p>Lorem Ipsum has been the industry's standard dummy text ever since the 1500s, when an unknown printer took a galley of type and scrambled it to make a type specimen book. It has survived not only five centuries, but also the leap into electronic typesetting, remaining essentially unchanged. It was popularised in the 1960s with the release of Brindell sheets containing Lorem Ipsum passages, and more recently with desktop publishing software like Quillmark Layout including versions of Lorem Ipsum</p>

    <h3 class="tight">3. Quisquam est qui dolorem ipsum quia</h3>
    <p>It is a long established fact that a reader will be distracted by the readable content of a page when looking at its layout. The point of using Lorem Ipsum is that it has a more-or-less normal distribution of letters, as opposed to using 'Content here, content here', making it look like readable English. Many desktop publishing packages and web page editors now use Lorem Ipsum as their default model text, and a search for 'lorem ipsum' will uncover many web sites still in their infancy. Various versions have evolved over the years, sometimes by accident, sometimes on purpose</p>

    <h3 class="tight">4. Porro quisquam est qui dolorem ipsum</h3>
    <p>It is a long established fact that a reader will be distracted by the readable content of a page when looking at its layout. The point of using Lorem Ipsum is that it has a more-or-less normal distribution of letters, as opposed to using 'Content here, content here', making it look like readable English. Many desktop publishing packages and web page editors now use Lorem Ipsum as their default model text, and a search for 'lorem ipsum' will uncover many web sites still in their infancy. Various versions have evolved over the years, sometimes by accident, sometimes on purpose</p>

    <h3 class="tight">5. Dolorem ipsum quia dolor sit amet,</h3>
    <p>It is a long established fact that a reader will be distracted by the readable content of a page when looking at its layout. The point of using Lorem Ipsum is that it has a more-or-less normal distribution of letters, as opposed to using 'Content here, content here', making it look like readable English. Many desktop publishing packages and web page editors now use Lorem Ipsum as their default model text, and a search for 'lorem ipsum' will uncover many web sites still in their infancy. Various versions have evolved over the years, sometimes by accident, sometimes on purpose</p>
  </article>
</main>

<footer class="footer">
  <div class="brand"><span>BROVLANE PASS</span></div>
  <div class="col col-contact">
    <h4>CONTACT US</h4>
    <p>Address : 2170 Harlow Crest Ave,<br>Dunmere, Fl, 33961<br>Phone : 555-310-4728<br>Email : hello@brovlanepass.net</p>
  </div>
  <div class="col col-mail">
    <h4>JOIN OUR MAILING LIST</h4>
    <p>Your about us information would fit here nicely.</p>
    <div class="signup"><span>Email address</span><b>Submit</b></div>
  </div>
  <div class="col col-follow">
    <h4>FOLLOW US OUT THERE</h4>
    <div class="social" aria-label="Social links"><i></i><i></i><i></i><i></i></div>
  </div>
  <div class="rule"></div>
  <p class="copyright">Copyright © 2017. All Rights Reserved</p>
</footer>
</body>
</html>
```